Fresh, modern, fun business card for pediatric dental practice

Need a business card for fresh, modern, fun pediatric dental practice

Clean look that matches our website's font and colors

We prefer the look of curved corners on business cards

Target Market(s)

parents (mothers) of young children, professionals, mid-high class

Industry/Entity Type

Dental

Contact Information for Business Card

Maplebrook Pediatric Dentistry
482 Quarry Lane
Suite 517
Cedar Hollow, PA 17580
717.555.0193
www.maplebrookkidsdental.example

Mei-Ran Tsai, DMD
Corinne Walbeck, DMD
(we are working on our email address, but we would like that on the card as well)

Font styles to use
Sans Serif

Requirements
Must have
• All info; we would also like to make cards for individual staff members
• colors from our website and color palatte, attatched
• use same font and design as website for branding
Nice to have
• clean, simple card that has a pop of color
• we would like to see a few designs with our tag line "where smiles get brighter"
• we are not sure if we want to have it on there or not
• we would like to see a few designs incorporating the ribbon graphic on our website where the word WELCOME is

```html
<!DOCTYPE html>
<html lang="en">
<head>
<meta charset="utf-8">
<title>Maplebrook Pediatric Dentistry – Business Card</title>
<link href="https://fonts.googleapis.com/css2?family=Work+Sans:wght@400;500;600&display=swap" rel="stylesheet">
<style>
  :root {
    --magenta: #cc2a96;
    --sun: #fdb515;
    --white: #ffffff;
    --photo-pink: #c968b4;
    --photo-deep: #b94f9f;
    --page: #e9e6e2;
    --radius: 24px;
  }
  * { margin: 0; padding: 0; box-sizing: border-box; }
  html, body { width: 1200px; height: 930px; overflow: hidden; }
  body {
    background: var(--page);
    font-family: "Work Sans", sans-serif;
    position: relative;
  }
  .card {
    position: absolute;
    left: 278px;
    width: 644px;
    height: 369px;
    border-radius: var(--radius);
    overflow: hidden;
    box-shadow: 0 4px 14px rgba(0,0,0,0.18);
  }
  .card-front { top: 75px; background: var(--magenta); }
  .card-back { top: 486px; }

  .front-curve { position: absolute; inset: 0; width: 100%; height: 100%; }

  .contact {
    position: absolute;
    left: 30px;
    top: 188px;
    color: var(--white);
  }
  .contact-name {
    font-size: 23px;
    font-weight: 600;
    letter-spacing: 0.3px;
    line-height: 1;
  }
  .contact-title {
    font-size: 14px;
    font-weight: 400;
    margin-top: 5px;
  }
  .contact-address {
    font-size: 14.5px;
    font-weight: 400;
    line-height: 19px;
    margin-top: 14px;
  }
  .contact-lines {
    list-style: none;
    margin-top: 9px;
    font-size: 14.5px;
    line-height: 19px;
  }
  .contact-lines li { display: flex; align-items: center; gap: 7px; }
  .contact-lines svg { width: 10px; height: 10px; flex: none; }

  .brand-front {
    position: absolute;
    right: 22px;
    top: 34px;
    width: 300px;
    text-align: center;
    color: var(--magenta);
    font-weight: 500;
  }
  .brand-dot {
    display: block;
    width: 50px;
    height: 50px;
    border-radius: 50%;
    background: var(--sun);
    margin: 0 auto 26px;
  }
  .brand-name { display: block; font-size: 42px; line-height: 1; letter-spacing: 0.5px; }
  .brand-sub { display: block; font-size: 22px; line-height: 1.2; margin-top: 6px; letter-spacing: 1.5px; }

  .back-photo {
    position: absolute;
    inset: 0;
    background: radial-gradient(ellipse at 50% 45%, var(--photo-deep) 0%, var(--photo-pink) 65%);
  }
  .brand-back {
    position: absolute;
    left: 0;
    right: 0;
    top: 92px;
    text-align: center;
    color: var(--white);
    font-weight: 500;
  }
  .brand-back .brand-dot { background: var(--white); width: 66px; height: 66px; margin-bottom: 30px; }
  .brand-back .brand-name { font-size: 58px; }
  .brand-back .brand-sub { font-size: 30px; letter-spacing: 2px; }
</style>
</head>
<body>

  <section class="card card-front">
    <svg class="front-curve" viewBox="0 0 644 369" preserveAspectRatio="none" aria-hidden="true">
      <path d="M218 0 C236 205 410 330 606 369 L644 369 L644 0 Z" fill="var(--white)"/>
      <path d="M221 0 C239 203 412 328 610 369 L644 369 L644 0 Z" fill="var(--sun)"/>
      <path d="M246 0 C262 185 420 322 614 369 L644 369 L644 0 Z" fill="var(--white)"/>
    </svg>

    <div class="brand-front">
      <span class="brand-dot"></span>
      <span class="brand-name">Maplebrook</span>
      <span class="brand-sub">Pediatric Dentistry</span>
    </div>

    <div class="contact">
      <h1 class="contact-name">CORINNE WALBECK</h1>
      <p class="contact-title">DMD</p>
      <p class="contact-address">482 Quarry Lane<br>Suite 517 Cedar Hollow, PA 17580</p>
      <ul class="contact-lines">
        <li>
          <svg viewBox="0 0 10 10" aria-hidden="true"><path d="M2 1 L4 1 L4.6 3 L3.5 3.8 C4 5.2 4.8 6 6.2 6.5 L7 5.4 L9 6 L9 8 C5 8.5 1.5 5 2 1 Z" fill="var(--white)"/></svg>
          717.555.0193
        </li>
        <li>
          <svg viewBox="0 0 10 10" aria-hidden="true"><rect x="1" y="2.5" width="8" height="5.5" fill="none" stroke="var(--white)" stroke-width="1.2"/><path d="M1 2.5 L5 5.5 L9 2.5" fill="none" stroke="var(--white)" stroke-width="1.2"/></svg>
          hello@maplebrookkidsdental.example
        </li>
        <li>
          <svg viewBox="0 0 10 10" aria-hidden="true"><circle cx="5" cy="5" r="4" fill="none" stroke="var(--white)" stroke-width="1"/><ellipse cx="5" cy="5" rx="1.8" ry="4" fill="none" stroke="var(--white)" stroke-width="0.9"/><path d="M1 5 H9" stroke="var(--white)" stroke-width="0.9"/></svg>
          www.maplebrookkidsdental.example
        </li>
      </ul>
    </div>
  </section>

  <section class="card card-back">
    <div class="back-photo" role="img" aria-label="Photo of a smiling young child with pigtails brushing her teeth, tinted pink"></div>
    <div class="brand-back">
      <span class="brand-dot"></span>
      <span class="brand-name">Maplebrook</span>
      <span class="brand-sub">Pediatric Dentistry</span>
    </div>
  </section>

</body>
</html>
```